Cool Website Design Gleam Shell Crew.

We need a new website, using our existing domain, with a similar function to https://www.marbeckfilm.com/ or https://www.tolvanfinishworks.com/ instagram gleam_shell.crew.
We can send google docs with pictures.
Logo attached

```html
<!DOCTYPE html>
<html lang="en">
<head>
<meta charset="utf-8">
<title>Gleam Shell Crew — Vehicle Wraps</title>
<link rel="stylesheet" href="https://fonts.googleapis.com/css2?family=Poppins:wght@500;600;700&family=Roboto:wght@400;500;700&display=swap">
<style>
:root{
  --bg:#000;
  --purple:#6b2fe0;
  --violet:#5a34dd;
  --blue:#2f62d8;
  --white:#fff;
  --muted:#d9d9e6;
  --line:#3a3a44;
  --star:#f2b01e;
  --grad:linear-gradient(90deg,var(--purple),var(--blue));
}
*{box-sizing:border-box;margin:0;padding:0}
html,body{width:1200px;height:5263px;overflow:hidden;background:var(--bg)}
body{position:relative;font-family:"Roboto",sans-serif;color:var(--white)}
.abs{position:absolute}
.grad-text{background:var(--grad);-webkit-background-clip:text;background-clip:text;color:transparent}
.btn{position:absolute;display:flex;align-items:center;justify-content:center;font:500 16px "Roboto",sans-serif;color:var(--white);text-transform:uppercase;background:var(--grad);clip-path:polygon(6% 0,100% 0,94% 100%,0 100%)}
.btn.white{background:var(--white);color:var(--violet)}
.btn.dark{background:#000;clip-path:none}
.photo{position:absolute}
.section-title{position:absolute;left:0;width:1200px;text-align:center;font:600 40px "Poppins",sans-serif;text-transform:uppercase}

/* header */
.brand{left:143px;top:38px;font:700 30px "Poppins",sans-serif;color:var(--violet);line-height:1.1;width:260px}
.nav{left:465px;top:100px;display:flex;gap:28px;font:400 15px "Roboto",sans-serif;text-transform:uppercase}
.nav .active{border-bottom:3px solid var(--blue);padding-bottom:6px}

/* hero */
.hero-title{left:143px;top:306px;width:560px;font:600 40px/49px "Poppins",sans-serif;text-transform:uppercase;white-space:nowrap}
.hero-text{left:143px;top:528px;width:470px;font:400 18px/30px "Roboto",sans-serif}
.call-btn{position:absolute;left:316px;top:625px;width:212px;height:55px;display:flex;align-items:center;justify-content:center;gap:12px;font:500 18px "Roboto",sans-serif}
.dots{left:143px;top:728px;display:flex;gap:12px}
.dots i{width:7px;height:7px;border-radius:50%;background:var(--white)}
.dots i:first-child{background:var(--blue)}

/* testimonials */
.review{position:absolute;top:1073px;width:224px;height:170px;border:1px solid #5a5a66;padding:18px 20px}
.review .who{display:flex;align-items:center;gap:10px}
.avatar{width:32px;height:32px;border-radius:50%;background:#3a3a3a;display:flex;align-items:center;justify-content:center;font-size:13px}
.name{font:700 11px "Roboto",sans-serif}
.stars{color:var(--star);font-size:11px;letter-spacing:1px}
.review p{margin-top:10px;font:italic 400 11px/17px "Roboto",sans-serif;color:var(--muted)}
.arrow{position:absolute;width:34px;height:34px;border:2px solid #bbb;border-radius:50%;display:flex;align-items:center;justify-content:center}

/* about */
.about-title{left:648px;top:1422px;font:600 40px "Poppins",sans-serif}
.about-text{left:648px;top:1500px;width:392px;font:400 15.5px/26.5px "Roboto",sans-serif;text-align:justify}

/* services */
.service{position:absolute;top:2150px;height:448px;border:1px solid #6a6a74}
.service.active{border-color:var(--blue)}
.service h3{position:absolute;top:272px;left:0;width:100%;text-align:center;font:500 18px/26px "Roboto",sans-serif;text-transform:uppercase}
.service p{position:absolute;top:330px;left:30px;right:30px;text-align:center;font:400 13.5px/23px "Roboto",sans-serif}

/* banner */
.banner{left:51px;top:2743px;width:1100px;height:395px;background:var(--grad);clip-path:polygon(7% 0,100% 0,93% 100%,0 100%)}
.stat{left:210px;top:2785px;font:700 66px "Poppins",sans-serif}
.stat-sub{left:210px;top:2872px;font:500 38px "Poppins",sans-serif;text-transform:uppercase}
.banner-text{left:210px;top:2943px;width:380px;font:400 16px/27px "Roboto",sans-serif}

/* gallery */
.thumb{position:absolute;width:222px;height:227px}

/* contact */
.contact-panel{left:527px;top:4018px;width:640px;height:550px;background:linear-gradient(110deg,#3453d8,#2f66dc);clip-path:polygon(3% 0,100% 0,96% 100%,0 100%)}
.field{position:absolute;background:var(--white);color:#444;font:400 12px "Roboto",sans-serif;padding:16px 28px;clip-path:polygon(4% 0,100% 0,96% 100%,0 100%)}

/* footer */
.foot-head{position:absolute;top:4858px;font:700 18px "Roboto",sans-serif;text-transform:uppercase}
.foot-list{position:absolute;top:4906px;list-style:none;font:400 14px/24px "Roboto",sans-serif}
.foot-info{position:absolute;left:497px;font:400 14px/24px "Roboto",sans-serif;display:flex;gap:18px;align-items:flex-start;width:290px}
.bottom-bar{left:0;top:5165px;width:1200px;height:61px;background:var(--grad);clip-path:polygon(3% 0,100% 0,100% 100%,0 100%)}
.social{position:absolute;top:5178px;width:36px;height:36px;border:2px solid var(--white);border-radius:50%}
</style>
</head>
<body>

<!-- header -->
<div class="abs brand">GLEAM SHELL<br>CREW</div>
<nav class="abs nav">
  <span class="active">Home</span><span>About</span><span>Gallery</span><span>Services</span><span>Contact</span>
</nav>
<div class="btn" style="left:905px;top:86px;width:144px;height:49px;font-size:15px">Get a Quote</div>

<!-- hero -->
<h1 class="abs hero-title grad-text">Protect your<br>paint or change<br>your colour without<br>breaking the bank.</h1>
<p class="abs hero-text">Sed ut perspiciatis unde omnis iste natus errosit voluptatem accusantium doloremque</p>
<div class="btn" style="left:143px;top:625px;width:165px;height:55px;font-size:16px">Get a Quote</div>
<svg class="abs" style="left:316px;top:625px" width="212" height="55"><polygon points="8,1 211,1 204,54 1,54" fill="none" stroke="#4b46e0" stroke-width="2"/></svg>
<div class="call-btn">
  <svg width="22" height="22" viewBox="0 0 24 24"><circle cx="12" cy="12" r="12" fill="#fff"/><path d="M8 6c1 0 2 2.5 2 3s-1 1-1 1.5 2 3.5 3.5 4c.5 0 1-1 1.5-1s3 1 3 2-1.5 2.5-2.5 2.5C9 18 6 13 6 9c0-1.5 1-3 2-3z" fill="#000"/></svg>
  +1 888 888 8888
</div>
<div class="abs dots"><i></i><i></i><i></i><i></i></div>
<div class="photo" role="img" aria-label="Black car with blue wrap accents parked on a snowy hillside" style="left:672px;top:220px;width:258px;height:603px;background:linear-gradient(180deg,#6b8fc0 0%,#e8ecf2 35%,#2a2e36 60%,#d7dbe2 100%);clip-path:polygon(0 6%,100% 0,100% 88%,0 100%)"></div>
<div class="photo" role="img" aria-label="Rear view of the same wrapped car in the snow" style="left:940px;top:220px;width:220px;height:603px;background:linear-gradient(180deg,#5f86c0 0%,#dfe5ee 30%,#1e2229 55%,#8a8f98 100%);clip-path:polygon(0 6%,100% 0,100% 88%,0 100%)"></div>

<!-- testimonials -->
<h2 class="section-title grad-text" style="top:967px;font-weight:500">What customers say about us</h2>
<div class="arrow" style="left:87px;top:1150px"><svg width="12" height="12" viewBox="0 0 12 12"><path d="M8 1 3 6l5 5" stroke="#ccc" stroke-width="2" fill="none"/></svg></div>
<div class="arrow" style="left:1077px;top:1150px"><svg width="12" height="12" viewBox="0 0 12 12"><path d="m4 1 5 5-5 5" stroke="#ccc" stroke-width="2" fill="none"/></svg></div>

<div class="review" style="left:147px"><div class="who"><div class="avatar">J</div><div><div class="name">JOHN DOE</div><div class="stars">★★★★★</div></div></div><p>"Sed ut perspiciatis unde omnis iste natus error sit voluptatem accusantium doloremque tium, totam rem aperiue ipsa quallo inventore verquasi architecto"</p></div>
<div class="review" style="left:377px"><div class="who"><div class="avatar">J</div><div><div class="name">JOHN DOE</div><div class="stars">★★★★★</div></div></div><p>"Sed ut perspiciatis unde omnis iste natus error sit voluptatem accusantium doloremque tium, totam rem aperiue ipsa quallo inventore verquasi architecto"</p></div>
<div class="review" style="left:607px"><div class="who"><div class="avatar">J</div><div><div class="name">JOHN DOE</div><div class="stars">★★★★★</div></div></div><p>"Sed ut perspiciatis unde omnis iste natus error sit voluptatem accusantium doloremque tium, totam rem aperiue ipsa quallo inventore verquasi architecto"</p></div>
<div class="review" style="left:837px"><div class="who"><div class="avatar">J</div><div><div class="name">JOHN DOE</div><div class="stars">★★★★★</div></div></div><p>"Sed ut perspiciatis unde omnis iste natus error sit voluptatem accusantium doloremque tium, totam rem aperiue ipsa quallo inventore verquasi architecto"</p></div>

<!-- about -->
<div class="abs" style="left:0;top:1370px;width:74px;height:547px;background:var(--purple);clip-path:polygon(45% 0,100% 0,55% 100%,0 100%)"></div>
<div class="photo" role="img" aria-label="Black pickup truck with red stripe wrap parked in a driveway" style="left:57px;top:1370px;width:470px;height:547px;background:linear-gradient(180deg,#6fa3dc 0%,#3f6b3c 30%,#1b1c20 55%,#8d8a82 100%);clip-path:polygon(5% 0,100% 0,100% 100%,0 100%)"></div>
<div class="abs" style="left:510px;top:1370px;width:74px;height:547px;background:var(--blue);clip-path:polygon(45% 0,100% 0,55% 100%,0 100%)"></div>
<h2 class="abs about-title grad-text">ABOUT US</h2>
<p class="abs about-text">Sed ut perspiciatis unde omnis iste natus error sit voluptatem accusantium doloremque laudantium, totam rem aperiam, eaque ipsa quae ab illo inventore veritatis et quasi architecto beatae vitae dicta sunt explicabo. Nemo enim ipsam voluptatem quia voluptas sit aspernatur aut odit aut fugit, sed quia consequuntur magni dolores eos qui ratione voluptatem sequi nesciunt. Neque porro quisquam esorem ipsum quia dolor sit amnsectetur</p>
<div class="btn" style="left:648px;top:1774px;width:162px;height:56px">Read More</div>

<!-- services -->
<h2 class="section-title grad-text" style="top:2050px">Our Services</h2>
<div class="arrow" style="left:87px;top:2370px"><svg width="12" height="12" viewBox="0 0 12 12"><path d="M8 1 3 6l5 5" stroke="#ccc" stroke-width="2" fill="none"/></svg></div>
<div class="arrow" style="left:1077px;top:2370px"><svg width="12" height="12" viewBox="0 0 12 12"><path d="m4 1 5 5-5 5" stroke="#ccc" stroke-width="2" fill="none"/></svg></div>

<div class="service" style="left:135px;width:302px">
  <div class="photo" role="img" aria-label="Car with a teal printed commercial wrap" style="left:10px;top:0;width:282px;height:240px;background:linear-gradient(180deg,#5d7f54 0%,#3fd0d0 55%,#2a6e70 100%)"></div>
  <h3>Printed Commercial<br>Wraps</h3>
  <p>Sed ut perspiciatis unde omnis iste natus error sit voluptatem cusant ium doloremque</p>
</div>
<div class="service active" style="left:445px;width:289px">
  <div class="photo" role="img" aria-label="Hatchback with a gold colour change wrap" style="left:12px;top:0;width:277px;height:240px;background:linear-gradient(180deg,#7a8a7a 0%,#c9b423 55%,#4d4a2a 100%)"></div>
  <h3>Color Change/<br>Custom Restyle</h3>
  <p>Sed ut perspiciatis unde omnis iste natus error sit voluptatem cusant ium doloremque</p>
</div>
<div class="service" style="left:754px;width:292px">
  <div class="photo" role="img" aria-label="Pickup truck with purple partial vinyl graphics" style="left:10px;top:0;width:282px;height:240px;background:linear-gradient(180deg,#7fa7d8 0%,#3a2b3e 50%,#9a2bbf 75%,#6d6a5a 100%)"></div>
  <h3>Vinyl Graphics /<br>Partial Wraps</h3>
  <p>Sed ut perspiciatis unde omnis iste natus error sit voluptatem cusant ium doloremque</p>
</div>
<div class="btn" style="left:214px;top:2571px;width:150px;height:51px">Read More</div>
<div class="btn" style="left:524px;top:2571px;width:150px;height:51px">Read More</div>
<div class="btn" style="left:832px;top:2571px;width:150px;height:51px">Read More</div>

<!-- banner -->
<div class="abs banner"></div>
<div class="abs stat">70000</div>
<div class="abs stat-sub">Views per day</div>
<p class="abs banner-text">Sed ut perspiciatis unde omnis iste natus erro sit voluptatem accusantium doloremque</p>
<div class="btn white" style="left:210px;top:3029px;width:155px;height:51px;clip-path:none">Get a Quote</div>
<div class="photo" role="img" aria-label="Sedan with a teal colour change wrap on an open field" style="left:609px;top:2763px;width:515px;height:354px;background:linear-gradient(180deg,#7ea9dc 0%,#c7d6e6 40%,#22a79b 65%,#7c8a58 100%);clip-path:polygon(5% 0,100% 0,95% 100%,0 100%)"></div>

<!-- gallery -->
<h2 class="section-title grad-text" style="top:3237px">Our Gallery</h2>
<div class="thumb" role="img" aria-label="Wrapped pickup front view" style="left:143px;top:3340px;background:linear-gradient(180deg,#6a8fbf,#1d2022 60%,#6b6b5e)"></div>
<div class="thumb" role="img" aria-label="Matte black car in a garage" style="left:373px;top:3340px;background:linear-gradient(180deg,#5a4e46,#1a1b1e 60%,#4a4640)"></div>
<div class="thumb" role="img" aria-label="Car with a teal patterned wrap" style="left:603px;top:3340px;background:linear-gradient(180deg,#8a4a3a,#1fa890 60%,#3a3a3a)"></div>
<div class="thumb" role="img" aria-label="Dark sports car with red hood accent" style="left:835px;top:3340px;background:linear-gradient(180deg,#9aa0a8,#2a2c30 50%,#c4344a 70%,#2a2c30)"></div>
<div class="thumb" role="img" aria-label="Black muscle car with blue stripes" style="left:143px;top:3583px;background:linear-gradient(180deg,#8a9aa8,#101418 55%,#2b5fd0 70%,#3a3a3a)"></div>
<div class="thumb" role="img" aria-label="Tail lights with red tint detail" style="left:373px;top:3583px;background:linear-gradient(180deg,#3a3a3e,#c0242c 50%,#2a2a2e)"></div>
<div class="thumb" role="img" aria-label="Teal wrapped hood close up" style="left:603px;top:3583px;background:linear-gradient(180deg,#2f7f98,#1a4a60 60%,#2b2b2b)"></div>
<div class="thumb" role="img" aria-label="Row of wrapped cars under a cloudy sky" style="left:835px;top:3583px;background:linear-gradient(180deg,#5b8ed2,#d8e2ee 50%,#3a3e44 75%,#7d8a5c)"></div>
<div class="btn" style="left:517px;top:3861px;width:164px;height:55px">View More</div>

<!-- contact -->
<div class="abs" style="left:34px;top:4018px;width:58px;height:550px;background:var(--purple);clip-path:polygon(60% 0,100% 0,40% 100%,0 100%)"></div>
<div class="photo" role="img" aria-label="Black muscle car parked under bare winter trees" style="left:76px;top:4018px;width:466px;height:550px;background:linear-gradient(180deg,#6d99d6 0%,#9aa5b0 35%,#151a22 65%,#6b6a62 100%);clip-path:polygon(4% 0,100% 0,100% 100%,0 100%)"></div>
<div class="abs contact-panel"></div>
<h2 class="abs" style="left:625px;top:4080px;font:600 40px 'Poppins',sans-serif">CONTACT US</h2>
<p class="abs" style="left:625px;top:4148px;width:380px;font:400 17px/26px 'Roboto',sans-serif">Call us at +1 888 888 8888 or message below to Book!</p>
<div class="field" style="left:627px;top:4231px;width:209px;height:47px">Enter Name</div>
<div class="field" style="left:844px;top:4231px;width:209px;height:47px">Enter Email</div>
<div class="field" style="left:627px;top:4292px;width:209px;height:45px">Enter Phone</div>
<div class="field" style="left:844px;top:4292px;width:209px;height:45px">Address</div>
<div class="field" style="left:627px;top:4350px;width:426px;height:71px;clip-path:polygon(2% 0,100% 0,98% 100%,0 100%)">Message</div>
<div class="btn dark" style="left:627px;top:4448px;width:146px;height:49px">Submit</div>

<!-- cta -->
<h2 class="abs grad-text" style="left:143px;top:4664px;font:600 32px 'Poppins',sans-serif;white-space:nowrap">PROTECT YOUR PAINT. LOOK GOOD DOING IT.</h2>
<div class="btn" style="left:875px;top:4658px;width:178px;height:57px">Wrap My Car</div>

<!-- footer -->
<div class="abs" style="left:143px;top:4783px;width:914px;height:1px;background:var(--line)"></div>
<div class="abs" style="left:440px;top:4783px;width:1px;height:370px;background:var(--line)"></div>
<div class="abs" style="left:797px;top:4783px;width:1px;height:370px;background:var(--line)"></div>

<h3 class="foot-head" style="left:143px">Serving Areas</h3>
<ul class="foot-list" style="left:143px">
  <li>Ceramic Coating</li><li>Color Change &amp; Custom Restyle</li><li>Printed Commercial Wraps</li><li>Promotional Unlimited</li><li>Vinyl Murals</li><li>Vinyl Graphics / Partial Wraps</li><li>Car Wraps</li><li>Signs</li>
</ul>

<h3 class="foot-head" style="left:497px">Address</h3>
<div class="foot-info" style="top:4906px"><svg width="16" height="16" viewBox="0 0 16 16" style="margin-top:4px;flex:none"><path d="M1 3l4-1.5 6 1.5 4-1.5v11l-4 1.5-6-1.5-4 1.5z" fill="#4a5fe0"/></svg><span>213,Sed ut perspiciatis unde omnis iste natus error sit voluptatem</span></div>
<div class="foot-info" style="top:4982px"><svg width="16" height="16" viewBox="0 0 16 16" style="margin-top:4px;flex:none"><path d="M4 1c1 0 2 3 2 3.5S5 5.5 5 6s2 4 4 5c.5 0 1-1 1.5-1S14 11 14 12s-1.5 3-2.5 3C6 15 1 10 1 4.5 1 3 2.5 1 4 1z" fill="#4a5fe0"/></svg><span>+ 1 888 888 8888</span></div>
<div class="foot-info" style="top:5030px"><svg width="16" height="16" viewBox="0 0 16 16" style="margin-top:4px;flex:none"><rect x="1" y="3" width="14" height="10" fill="#4a5fe0"/><path d="M1 3l7 6 7-6" stroke="#000" fill="none"/></svg><span>info@companyname.com</span></div>

<h3 class="foot-head" style="left:871px">Useful Links</h3>
<ul class="foot-list" style="left:871px">
  <li>Financing</li><li>Gallery</li><li>Blog</li><li>Jobs</li><li>Warranty</li><li>Contact Us</li>
</ul>

<div class="abs bottom-bar"></div>
<p class="abs" style="left:143px;top:5186px;font:400 14px 'Roboto',sans-serif">© 2025 Gleam Shell Crew. All rights reserved &nbsp;|&nbsp; Privacy Policy &nbsp;|&nbsp; Terms of use</p>
<div class="social" role="img" aria-label="Social profile link" style="left:922px"></div>
<div class="social" role="img" aria-label="Social profile link" style="left:969px"></div>
<div class="social" role="img" aria-label="Social profile link" style="left:1016px"></div>

</body>
</html>
```